Product label for herbal salves, lotions, soaps and tinctures

We need a very simple, clean and organic looking label that can be used for an ointment jar, a lotion bottle and a dropper bottle.
We have an existing logo (see attached). We like the colors white, olive green, gold and black. It needs to include product name as dominant and logo. It also needs to include an ingredient list, and usage statement. Include weight of product, distributed by, made in the USA, and QVX statement.
Example of what needs to be present:
Logo
Name: Tranquil Ease Blend
Used for: For Muscle Aches, Arthritis, Tendonitis, Headaches
To Use: For muscle aches, arthritis and tendonitis, massage into affected area. For tension headache apply to neck, temples and forehead.
Store in a cool and dry place, away from direct heat and sunlight.
Weight of product: 1.75
DIST. BY: Copper Brook Herbal
Made in the USA
This product is not intended to diagnose, treat, cure
or prevent any disease. Not regulated
by the QVX. Please consult your health care practitioner
before using product. Discontinue use if any adverse reaction occurs.
Ingredient list:
Wildcrafted Ingredients:
Ashwagandha Root, Peppermint Leaf, Hops Flowers, St. John’s Wort Herb, Arnica Flowers, Green Tea Leaf, Alfalfa Leaf, Dandelion Root, Burdock Root, Chickweed Herb, Chaparral Leaf, Yarrow Flowers, Boneset Herb, Moringa Leaf, Meadowsweet Herb, Nettle Leaf
Organic Ingredients:
Olive Oil, Aloe Leaf, Sweet Birch Bark, Helichrysum Flowers, Holy Basil Leaf, Borage Herb, Ginger Root, Angelica Root, White Willow Bark, Mustard Seed, Beeswax, Vitamin E, Essential Oils
Dimensions of Jar:
Circumference: 7 in.
Height: 1 in.

```html
<!DOCTYPE html>
<html lang="en">
<head>
<meta charset="utf-8">
<title>Tranquil Ease Blend – Label</title>
<link href="https://fonts.googleapis.com/css2?family=Barlow:ital,wght@0,400;0,500;0,600;0,700;1,600;1,700&family=Barlow+Semi+Condensed:wght@400&display=swap" rel="stylesheet">
<style>
  :root{
    --paper:#ffffff;
    --ink:#1b1b1b;
    --olive:#6f7231;
    --olive-soft:#8a8c52;
    --dieline:#e8463f;
  }
  *{box-sizing:border-box;margin:0;padding:0}
  html,body{width:1200px;height:1157px;overflow:hidden;background:var(--paper)}
  body{font-family:"Barlow",sans-serif;color:var(--ink);position:relative}
  .label{
    position:absolute;left:40px;top:506px;
    width:1836px;height:236px;
    transform:scale(0.61);transform-origin:0 0;
    border:1.5px solid var(--dieline);
    background:var(--paper);
  }
  .ingredients{
    position:absolute;left:28px;top:18px;width:504px;
    font-size:17px;line-height:18.2px;text-align:justify;
  }
  .ingredients h2{font-size:17px;font-weight:600;line-height:18px}
  .ingredients h3{font-size:17px;font-style:italic;font-weight:700;color:var(--olive);line-height:18px}
  .product-name{
    position:absolute;left:627px;top:44px;
    font-size:38px;font-weight:600;letter-spacing:4.6px;white-space:nowrap;
  }
  .brand{
    position:absolute;left:690px;top:138px;width:210px;
    display:flex;align-items:center;gap:8px;
    font-size:24px;font-weight:600;color:var(--olive);line-height:26px;
  }
  .brand .dot{width:14px;height:14px;border-radius:50%;background:var(--olive);flex:none}
  .uses{
    position:absolute;left:917px;top:125px;
    border-left:1.5px solid var(--ink);padding-left:14px;
    font-size:17px;line-height:22px;
  }
  .directions{
    position:absolute;left:1210px;top:28px;width:290px;
    font-size:17px;line-height:18px;text-align:justify;
  }
  .directions em{font-style:italic;font-weight:600;color:var(--olive)}
  .directions p+p{margin-top:18px}
  .disclaimer{
    position:absolute;left:1537px;top:28px;width:249px;
    font-family:"Barlow Semi Condensed",sans-serif;
    font-size:15px;line-height:14.5px;text-align:justify;
  }
  .origin{
    position:absolute;left:1560px;top:146px;width:226px;text-align:center;
    font-size:17px;font-style:italic;font-weight:700;color:var(--olive-soft);
  }
  .distributor{
    position:absolute;left:1545px;top:170px;width:241px;text-align:center;
    font-size:17px;line-height:24px;
  }
  .distributor strong{font-weight:600}
  .weight{
    position:absolute;left:1347px;top:196px;
    font-size:17px;font-weight:600;
  }
  .mark{
    position:absolute;left:1496px;top:192px;width:18px;height:18px;border-radius:50%;
    background:var(--olive);
  }
</style>
</head>
<body>
  <section class="label">
    <div class="ingredients">
      <h2>INGREDIENT LIST:</h2>
      <h3>Wildcrafted Ingredients:</h3>
      <p>Ashwagandha Root, Peppermint Leaf, Hops Flowers, St. John’s Wort Herb, Arnica Flowers, Green Tea Leaf, Alfalfa Leaf, Dandelion Root, Burdock Root, Chickweed Herb, Chaparral Leaf, Yarrow Flowers, Boneset Herb, Moringa Leaf, Meadowsweet Herb, Nettle Leaf.</p>
      <h3>Organic Ingredients:</h3>
      <p>Olive Oil, Aloe Leaf, Sweet Birch Bark, Helichrysum Flowers, Holy Basil Leaf, Borage Herb, Ginger Root, Angelica Root, White Willow Bark, Mustard Seed, Beeswax, Vitamin E, Essential Oils.</p>
    </div>

    <h1 class="product-name">TRANQUIL EASE BLEND</h1>

    <div class="brand"><span class="dot"></span><span>Copper Brook Herbal</span></div>

    <ul class="uses" style="list-style:none">
      <li>Muscle Aches</li>
      <li>Arthritis</li>
      <li>Tendonitis</li>
      <li>Headaches</li>
    </ul>

    <div class="directions">
      <p><em>To Use:</em> For muscle aches, arthritis and tendonitis, massage into affected area. For tension headache apply to neck, temples and forehead.</p>
      <p>Store in a cool and dry place, away from direct heat and sunlight.</p>
    </div>

    <p class="disclaimer">This product is not intended to diagnose, treat, cure or prevent any disease. Not regulated by the QVX. Please consult your health care practitioner before using product. Discontinue use if any adverse reaction occurs.</p>

    <p class="origin">- Made in the USA -</p>

    <div class="distributor">
      <strong>DIST. BY: COPPER BROOK HERBAL</strong><br>
      www.copperbrookherbal.com
    </div>

    <span class="mark"></span>
    <p class="weight">WEIGHT: 1.75 OZ</p>
  </section>
</body>
</html>
```